ebook cover for The Heron & The Teapot (Plink!)

We would like an ebook cover for a post Ph.D. on Animal Totems book called The Heron and The Teapot. It is about human relationships and dating. Author is Marla Wendlow Ph.D.
I am thinking perhaps just typographic with a fancy custom italicized or handwriting kind of font that fills the whole page, or a picture that doesn't belittle the fairytale of love. Something cosmic.
The subtitle to guide people, small, is "on dating"

```html
<!DOCTYPE html>
<html lang="en">
<head>
<meta charset="utf-8">
<title>The Heron and The Teapot — Marla Wendlow Ph.D.</title>
<link rel="stylesheet" href="https://fonts.googleapis.com/css2?family=Alegreya:wght@400&family=Cinzel:wght@500;600&family=Cormorant+Garamond:wght@500&display=swap">
<style>
  :root {
    --sky-top: #2a0a16;
    --sky-mid: #3d2426;
    --sky-low: #5a5444;
    --sky-haze: #7a7f62;
    --glow: #f4ecbc;
    --star: #efe0b4;
    --author: #f0dfb3;
    --gold-light: #fbe7a0;
    --gold-mid: #d6ac4c;
    --gold-dark: #8a6420;
    --subtitle: #d2c08c;
    --warm-orange: #d98a5e;
    --warm-orange-deep: #c47048;
    --tan: #d8bf80;
    --tan-deep: #b89a5c;
    --hat-brown: #5a2a2a;
  }
  * { margin: 0; padding: 0; box-sizing: border-box; }
  html, body { width: 754px; height: 1200px; overflow: hidden; background: var(--sky-top); }
  .cover {
    position: relative;
    width: 754px;
    height: 1200px;
    overflow: hidden;
    background: linear-gradient(to bottom,
      var(--sky-top) 0%,
      var(--sky-mid) 30%,
      var(--sky-low) 52%,
      var(--sky-haze) 64%,
      #8c9270 74%,
      #9a9e78 100%);
  }
  .stars { position: absolute; inset: 0; width: 754px; height: 1200px; }
  .stars path { fill: var(--star); }
  .author {
    position: absolute;
    top: 112px; left: 0; width: 100%;
    text-align: center;
    font-family: "Alegreya", serif;
    font-size: 46px;
    color: var(--author);
    letter-spacing: -0.5px;
    line-height: 1;
  }
  .title {
    position: absolute;
    left: 0; width: 100%;
    text-align: center;
    font-family: "Cinzel", serif;
    font-weight: 600;
    background: linear-gradient(to bottom, var(--gold-light) 0%, var(--gold-mid) 55%, var(--gold-dark) 100%);
    -webkit-background-clip: text;
    background-clip: text;
    color: transparent;
    filter: drop-shadow(2px 3px 3px rgba(0,0,0,0.55));
    line-height: 1;
    white-space: nowrap;
  }
  .title-line { top: 286px; font-size: 104px; }
  .title-line--second { top: 492px; font-size: 100px; }
  .title-joiner { top: 410px; font-size: 44px; }
  .subtitle {
    position: absolute;
    top: 618px; left: 0; width: 100%;
    text-align: center;
    font-family: "Cormorant Garamond", serif;
    font-weight: 500;
    font-size: 62px;
    line-height: 1;
    color: var(--subtitle);
    text-shadow: 1px 2px 3px rgba(0,0,0,0.35);
  }
  .artwork {
    position: absolute;
    left: 0; top: 700px;
    width: 754px; height: 500px;
    background:
      radial-gradient(ellipse 34% 46% at 22% 82%, rgba(244,236,188,0.9), transparent 75%),
      radial-gradient(ellipse 36% 58% at 73% 62%, rgba(244,236,188,0.85), transparent 75%);
  }
  .artwork-figure {
    position: absolute;
    box-shadow: 0 0 40px 14px rgba(244,236,188,0.55);
  }
  .artwork-figure--left {
    left: 22px; top: 150px;
    width: 300px; height: 360px;
    border-radius: 46% 46% 10px 10px / 30% 30% 10px 10px;
    background: linear-gradient(to bottom, var(--warm-orange-deep) 0%, var(--warm-orange) 30%, #e0a070 70%, var(--warm-orange-deep) 100%);
  }
  .artwork-figure--right {
    left: 400px; top: 56px;
    width: 300px; height: 460px;
    border-radius: 40% 40% 10px 10px / 16% 16% 10px 10px;
    background: linear-gradient(to bottom, var(--hat-brown) 0%, var(--hat-brown) 28%, var(--tan) 36%, #e2cc90 70%, var(--tan-deep) 100%);
  }
</style>
</head>
<body>
  <main class="cover">
    <svg class="stars" viewBox="0 0 754 1200" aria-hidden="true">
      <defs>
        <path id="star" d="M0,-15 L4.4,-4.6 L14.3,-4.6 L6.3,2.3 L9.3,13 L0,6.8 L-9.3,13 L-6.3,2.3 L-14.3,-4.6 L-4.4,-4.6 Z"/>
      </defs>
      <use href="#star" x="20" y="20"/>
      <use href="#star" x="192" y="70"/>
      <use href="#star" x="426" y="84"/>
      <use href="#star" x="632" y="52"/>
      <use href="#star" x="578" y="178"/>
      <use href="#star" x="708" y="194"/>
      <use href="#star" x="78" y="370"/>
      <use href="#star" x="250" y="395"/>
      <use href="#star" x="684" y="406"/>
    </svg>

    <p class="author">Marla Wendlow Ph.D.</p>

    <h1>
      <span class="title title-line">The Heron</span>
      <span class="title title-joiner">AND</span>
      <span class="title title-line title-line--second">The Teapot</span>
    </h1>

    <p class="subtitle">on dating</p>

    <div class="artwork" role="img" aria-label="Illustration of a heron and a teapot side by side in a warm glow">
      <div class="artwork-figure artwork-figure--left"></div>
      <div class="artwork-figure artwork-figure--right"></div>
    </div>
  </main>
</body>
</html>
```